Harborline Auto LLC

Car Dealer Customer Service
Address: 2874 Cresthaven Road, Shelbyville, TN 37162
web: www.harborlineautoxq.net
email: harborlineautoxq@mailnest.example
Phone: (931) 555-0148
Phone: (629) 555-0173

```html
<!DOCTYPE html>
<html lang="en">
<head>
<meta charset="utf-8">
<title>Harborline Auto – Business Card</title>
<link href="https://fonts.googleapis.com/css2?family=Lexend:wght@700&family=Source+Sans+3:wght@400&display=swap" rel="stylesheet">
<style>
  :root{
    --page:#ffffff;
    --brand-blue:#1b6fa6;
    --deep-blue:#0a76b0;
    --brand-orange:#f2ab2a;
    --pale:#fdf3d2;
    --sky:#c9dcf0;
    --card-shadow:rgba(0,0,0,.28);
  }
  *{margin:0;padding:0;box-sizing:border-box}
  html,body{width:1200px;height:900px;overflow:hidden;background:var(--page)}
  .card{
    position:absolute;left:285px;width:630px;height:360px;
    box-shadow:0 6px 14px var(--card-shadow);
    overflow:hidden;
  }
  .card--front{
    top:63px;
    background:
      radial-gradient(ellipse 55% 70% at 50% 50%, rgba(255,255,255,.95) 0%, rgba(255,255,255,0) 70%),
      linear-gradient(180deg, var(--deep-blue) 0%, #7a9aaa 35%, #d9b36a 65%, var(--brand-orange) 100%);
  }
  .card--front::before{
    content:"";position:absolute;inset:0;
    background:
      radial-gradient(ellipse 40% 55% at 50% 0%, rgba(220,234,248,.9) 0%, rgba(220,234,248,0) 100%),
      radial-gradient(ellipse 45% 45% at 50% 100%, rgba(255,240,180,.9) 0%, rgba(255,240,180,0) 100%);
  }
  .front-mark{
    position:absolute;left:50%;top:112px;width:96px;height:96px;margin-left:-48px;
    border-radius:50%;background:var(--brand-blue);
  }
  .front-name{
    position:absolute;left:0;right:0;top:226px;text-align:center;
    font-family:"Lexend",sans-serif;font-weight:700;font-size:30px;
    color:var(--brand-blue);letter-spacing:.5px;
  }
  .card--back{top:477px;background:#fff}
  .brand{position:absolute;right:24px;top:32px;text-align:right}
  .brand-mark{
    display:block;margin:0 0 12px auto;margin-right:52px;
    width:86px;height:86px;border-radius:50%;background:var(--brand-blue);
  }
  .brand-name{
    font-family:"Lexend",sans-serif;font-weight:700;font-size:21px;
    color:var(--brand-blue);line-height:1;
  }
  .brand-tagline{
    font-family:"Source Sans 3",sans-serif;font-size:13px;
    color:var(--brand-orange);margin-top:5px;line-height:1;
  }
  .divider{position:absolute;left:26px;width:578px;top:203px;height:2px;background:var(--brand-orange)}
  .contact{
    position:absolute;font-family:"Source Sans 3",sans-serif;
    color:var(--brand-blue);font-size:18px;line-height:21px;
  }
  .icon{position:absolute;width:27px;height:27px}
  .contact-text{position:absolute;white-space:nowrap}
</style>
</head>
<body>

<section class="card card--front" aria-label="Card front">
  <span class="front-mark"></span>
  <h1 class="front-name">HARBORLINE AUTO</h1>
</section>

<section class="card card--back" aria-label="Card back">
  <div class="brand">
    <span class="brand-mark"></span>
    <div class="brand-name">HARBORLINE AUTO</div>
    <div class="brand-tagline">CAR DEALER CUSTOMER SERVICE</div>
  </div>

  <div class="divider"></div>

  <div class="contact">
    <svg class="icon" style="left:29px;top:227px" viewBox="0 0 28 28" aria-hidden="true">
      <rect width="28" height="28" rx="5" fill="var(--brand-blue)"/>
      <path d="M9 6c1 0 2 3 2.5 4.5.3 1-1.5 2-1.2 2.8.8 2 2.4 3.6 4.4 4.4.8.3 1.8-1.5 2.8-1.2C19 17 22 18 22 19c0 2-2 3.5-3.5 3.5C12 22.5 5.5 16 5.5 9.5 5.5 8 7 6 9 6z" fill="#fff"/>
    </svg>
    <div class="contact-text" style="left:74px;top:219px">(931) 555-0148</div>
    <div class="contact-text" style="left:74px;top:241px">(629) 555-0173</div>

    <svg class="icon" style="left:29px;top:262px" viewBox="0 0 28 28" aria-hidden="true">
      <rect width="28" height="28" rx="5" fill="var(--brand-blue)"/>
      <rect x="5" y="8" width="18" height="12" fill="none" stroke="#fff" stroke-width="2"/>
      <path d="M5 8l9 8 9-8" fill="none" stroke="#fff" stroke-width="2"/>
    </svg>
    <div class="contact-text" style="left:74px;top:264px;font-size:16px">harborlineautoxq@mailnest.example</div>

    <svg class="icon" style="left:29px;top:296px" viewBox="0 0 28 28" aria-hidden="true">
      <rect width="28" height="28" rx="5" fill="var(--brand-blue)"/>
      <circle cx="14" cy="14" r="8.5" fill="none" stroke="#fff" stroke-width="1.8"/>
      <ellipse cx="14" cy="14" rx="3.5" ry="8.5" fill="none" stroke="#fff" stroke-width="1.6"/>
      <path d="M5.5 14h17" stroke="#fff" stroke-width="1.6"/>
    </svg>
    <div class="contact-text" style="left:74px;top:298px">www.harborlineautoxq.net</div>

    <svg class="icon" style="left:386px;top:226px" viewBox="0 0 28 28" aria-hidden="true">
      <rect width="28" height="28" rx="5" fill="var(--brand-blue)"/>
      <path d="M14 5a6.5 6.5 0 0 1 6.5 6.5C20.5 16 14 22 14 22s-6.5-6-6.5-10.5A6.5 6.5 0 0 1 14 5z" fill="#fff"/>
      <circle cx="14" cy="11.5" r="2.4" fill="var(--brand-blue)"/>
    </svg>
    <div class="contact-text" style="left:430px;top:219px;font-size:17px;line-height:23px">
      2874 Cresthaven Road,<br>Shelbyville,<br>TN 37162
    </div>
  </div>
</section>

</body>
</html>
```